Vantro cards

I am in the auto motive, transportation business I would like a business card that is Something cool, modern edgy, having to do with car culture. I offer towing service for high and exotic cars. I also provide towing for collisions and car accidents. I offer open and enclosed transport nationwide.

Target Market(s)

Car culture people high end auto collectors

Industry/Entity Type

Towing car carrier

Contact Information for Business Card

My company colors black yellow and silver

Font styles to use
Serif

```html
<!DOCTYPE html>
<html lang="en">
<head>
<meta charset="utf-8">
<title>Vantro Transportation — Business Cards</title>
<link rel="stylesheet" href="https://fonts.googleapis.com/css2?family=Montserrat:wght@400;600;800&display=swap">
<style>
  :root {
    --backdrop: #e4e1dc;
    --ink: #000000;
    --paper: #ffffff;
    --signal-yellow: #f6dc4f;
    --silver-light: #f4f4f4;
    --silver-mid: #c9c9c9;
    --silver-dark: #8e8e8e;
    --muted-white: #e9e9e9;
  }
  * { margin: 0; padding: 0; box-sizing: border-box; }
  html, body { width: 900px; height: 1200px; overflow: hidden; }
  body {
    background: var(--backdrop);
    position: relative;
    font-family: "Montserrat", Arial, sans-serif;
  }
  .card {
    position: absolute;
    left: 80px;
    width: 742px;
    height: 442px;
    border-radius: 36px;
    overflow: hidden;
  }
  /* Front */
  .card-front { top: 130px; background: var(--ink); }
  .front-brand-panel {
    position: absolute; left: 0; top: 0;
    width: 372px; height: 100%;
    background: var(--paper);
    display: flex; align-items: center; justify-content: center;
  }
  .accent-tab {
    position: absolute; left: 372px; top: 188px;
    width: 6px; height: 72px;
    background: var(--signal-yellow);
    border-radius: 0 3px 3px 0;
  }
  .brand-name {
    display: flex; align-items: center; gap: 12px;
    font-weight: 800;
    color: var(--ink);
    font-size: 30px;
    letter-spacing: 0.5px;
    text-transform: uppercase;
  }
  .brand-mark {
    width: 22px; height: 22px;
    background: var(--signal-yellow);
  }
  .contact-block {
    position: absolute; left: 408px; top: 106px;
    color: var(--paper);
  }
  .person-name {
    color: var(--signal-yellow);
    font-weight: 600;
    font-size: 26px;
    line-height: 1.1;
  }
  .person-role { font-size: 16px; margin-top: 4px; color: var(--muted-white); }
  .contact-list { list-style: none; margin-top: 30px; }
  .contact-list li {
    display: flex; align-items: center; gap: 10px;
    font-size: 16.5px; line-height: 21px;
  }
  .contact-list svg { width: 14px; height: 14px; flex: none; }
  .postal-address { font-style: normal; font-size: 16.5px; line-height: 21px; margin-top: 22px; }

  /* Back */
  .card-back {
    top: 638px;
    background:
      conic-gradient(from 10deg at 50% 45%,
        var(--silver-light), var(--silver-dark) 12%, var(--silver-light) 24%,
        var(--silver-mid) 36%, var(--silver-light) 48%, var(--silver-dark) 60%,
        var(--silver-light) 72%, var(--silver-mid) 86%, var(--silver-light));
  }
  .back-brand {
    position: absolute; left: 0; right: 0; top: 176px;
    display: flex; justify-content: center;
  }
  .back-brand .brand-name { font-size: 34px; }
  .back-stripe {
    position: absolute; left: 0; right: 0; top: 364px;
    height: 5px; background: var(--signal-yellow);
  }
  .back-footer {
    position: absolute; left: 0; right: 0; bottom: 0;
    height: 60px; background: var(--ink);
    display: flex; align-items: center; justify-content: center;
    color: var(--muted-white); font-size: 16px;
  }
</style>
</head>
<body>

<section class="card card-front">
  <div class="front-brand-panel">
    <div class="brand-name"><span class="brand-mark"></span>Vantro Transportation</div>
  </div>
  <div class="accent-tab"></div>
  <div class="contact-block">
    <h1 class="person-name">Dana Whitlock</h1>
    <p class="person-role">Owner</p>
    <ul class="contact-list">
      <li>
        <svg viewBox="0 0 14 14" aria-hidden="true"><path fill="#f6dc4f" d="M1 4c0-2 2-3 6-3s6 1 6 3v1h-3V4H4v1H1zM3 6h8l2 6H1zM7 7.5a1.8 1.8 0 1 0 0 3.6 1.8 1.8 0 0 0 0-3.6z"/></svg>
        (555) 214-7390
      </li>
      <li>
        <svg viewBox="0 0 14 14" aria-hidden="true"><path fill="#f6dc4f" d="M1 3h12v8H1z"/><path d="M1 3l6 5 6-5" fill="none" stroke="#000" stroke-width="1.2"/></svg>
        info@vantrotransportation.com
      </li>
      <li>
        <svg viewBox="0 0 14 14" aria-hidden="true"><circle cx="7" cy="7" r="6" fill="#f6dc4f"/><path d="M4 4c1 1 2 1 2 2s-2 1-1 3 2 2 2 3M9 2c0 2 2 2 3 3" fill="none" stroke="#000" stroke-width="1"/></svg>
        www.vantrotransportation.com
      </li>
    </ul>
    <address class="postal-address">48 Harbor Road<br>Millbrook, PA 17012</address>
  </div>
</section>

<section class="card card-back">
  <div class="back-brand">
    <div class="brand-name"><span class="brand-mark"></span>Vantro Transportation</div>
  </div>
  <div class="back-stripe"></div>
  <div class="back-footer">www.vantrotransportation</div>
</section>

</body>
</html>
```